New Business Card Design Project LORVANTI-Italy

we are LORVANTI-Italy
our company in the market for 3 years we are luxury cosmetic company and its about time for a facelift :)
i will like to have elegant luxurious and unique business card
that will give the person that get it a unique, luxurious and elegant impression
I'm VERY OPEN FOR NEW IDEAS , even duo i add a few files of things that i see on line and i like them

i add my logo as well
my website is LORVANTI.COM
(if you would like to see the main style that we have)

Target Market(s)

adult that have money :)

Industry/Entity Type

Business

Contact Information for Business Card

Name - Dario Lorvanti
Position - CEO and CO Founder
address - 4817 E Halvern
telephone - 555-384-1926
email - dario@lorvanti.com
fax - 555-384-1926
website - LORVANTI.COM

Colors
000000
959595
fbee3e
ffffff

Requirements
Must have
• big logo in GOLD color
• elegant look
• impressive
Nice to have
• not must but maybe classy pattern background
• not must but maybe emblem
• maybe clear plastic business card
Should not have
• colors
• images

```html
<!DOCTYPE html>
<html lang="en">
<head>
<meta charset="utf-8">
<title>LORVANTI Italy – Business Card</title>
<link rel="stylesheet" href="https://fonts.googleapis.com/css2?family=Roboto:wght@400;500;700&display=swap">
<style>
  :root {
    --backdrop: #2b2b2d;
    --card-black: #141414;
    --gold-light: #fbee3e;
    --gold-mid: #d9b43a;
    --gold-deep: #a87d1c;
    --ink: #0a0a0a;
    --white: #ffffff;
    --grey: #959595;
  }
  * { margin: 0; padding: 0; box-sizing: border-box; }
  html, body {
    width: 1200px;
    height: 900px;
    overflow: hidden;
    background: var(--backdrop);
    font-family: "Roboto", Arial, sans-serif;
  }
  .stage {
    width: 1200px;
    height: 900px;
    display: flex;
    flex-direction: column;
    align-items: center;
    justify-content: center;
    gap: 28px;
  }
  .card {
    position: relative;
    width: 640px;
    height: 366px;
    background: var(--card-black);
    box-shadow: 0 14px 30px rgba(0, 0, 0, 0.45);
    overflow: hidden;
  }

  /* Front */
  .card--front {
    display: flex;
    flex-direction: column;
    align-items: center;
    justify-content: center;
    gap: 22px;
  }
  .brand-disc {
    width: 88px;
    height: 88px;
    border-radius: 50%;
    border: 3px solid var(--gold-mid);
  }
  .brand-name {
    font-weight: 500;
    font-size: 46px;
    letter-spacing: 4px;
    color: var(--gold-mid);
    line-height: 1;
  }

  /* Back */
  .gold-band {
    position: absolute;
    left: 0;
    top: 58px;
    width: 100%;
    height: 124px;
    background: linear-gradient(100deg, var(--gold-deep) 0%, var(--gold-light) 22%, var(--gold-mid) 48%, var(--gold-light) 72%, var(--gold-deep) 100%);
  }
  .holder {
    position: absolute;
    left: 40px;
    top: 30px;
    color: var(--ink);
  }
  .holder-name {
    font-weight: 700;
    font-size: 27px;
    letter-spacing: 0.5px;
    line-height: 1.1;
  }
  .holder-role {
    font-weight: 400;
    font-size: 17px;
    margin-top: 4px;
  }
  .band-disc {
    position: absolute;
    right: 32px;
    top: 12px;
    width: 100px;
    height: 100px;
    border-radius: 50%;
    border: 3px solid var(--ink);
  }
  .contact {
    position: absolute;
    left: 0;
    right: 0;
    top: 226px;
    text-align: center;
    color: var(--white);
    font-size: 17px;
    line-height: 29px;
  }
  .contact-label { color: var(--gold-mid); font-weight: 500; }
  .contact-web {
    color: var(--gold-mid);
    font-weight: 700;
    letter-spacing: 0.5px;
  }
</style>
</head>
<body>
  <main class="stage">
    <section class="card card--front" aria-label="Card front">
      <div class="brand-disc"></div>
      <div class="brand-name">LORVANTI</div>
    </section>

    <section class="card card--back" aria-label="Card back">
      <div class="gold-band">
        <div class="holder">
          <div class="holder-name">DARIO LORVANTI</div>
          <div class="holder-role">CEO &amp; CO Founder</div>
        </div>
        <div class="band-disc"></div>
      </div>
      <div class="contact">
        <div class="contact-address">4817 E Halvern</div>
        <div class="contact-lines">
          <span class="contact-label">P:</span> 555-384-1926
          <span class="contact-label">F:</span> 555-384-1926
          <span class="contact-label">E:</span> dario@lorvanti.com
        </div>
        <div class="contact-web">WWW.LORVANTI.COM</div>
      </div>
    </section>
  </main>
</body>
</html>
```